Quran Jar

So I need help designing bespoke jars which will contain religious quotes.

So there will be three jars in total sold either individually or in two or as a three.

Each Jar will have different contents and preferably a different colour scheme.

I want the packaging to be customised with my branding and logo and to make the product stand out I am thinking of packing it further in a cotton bag with my branding.

```html
<!DOCTYPE html>
<html lang="en">
<head>
<meta charset="utf-8">
<title>Serene Verses – Jar Labels and Tote Prints</title>
<link href="https://fonts.googleapis.com/css2?family=Quicksand:wght@600&family=Raleway:wght@300&family=Montserrat:wght@500&display=swap" rel="stylesheet">
<style>
  :root {
    --page: #ffffff;
    --rule: #e2e2e2;
    --quran: #284b3a;
    --quran-band: #1c3629;
    --hadith: #84651a;
    --hadith-band: #5e4710;
    --dua: #ffffff;
    --dua-band: #d9d9d9;
    --gold-light: #f3d577;
    --gold-deep: #7a5a14;
    --ink-light: #f4f1e6;
    --ink-dark: #3a3a3a;
    --m-happiness: #f5d327;
    --m-sadness: #8fd0ef;
    --m-anxiety: #a35ee0;
    --m-gratefulness: #7ed87e;
    --m-patience: #f0961a;
    --m-hope: #f4bfd0;
    --m-forgiveness: #e6e6e6;
    --m-love: #e8190f;
  }
  * { box-sizing: border-box; margin: 0; padding: 0; }
  html, body { width: 1118px; height: 1200px; overflow: hidden; background: var(--page); }
  .sheet { position: relative; width: 1118px; height: 1200px; }

  .divider { position: absolute; left: 87px; width: 934px; height: 1px; background: var(--rule); }
  .divider--one { top: 438px; }
  .divider--two { top: 744px; }

  /* Label */
  .label {
    position: absolute; width: 237px; height: 159px; overflow: hidden;
    text-align: center; color: var(--ink-light);
    --bg: var(--quran); --band: var(--quran-band); --accent: var(--gold-light); --title: var(--ink-light);
    background: var(--bg);
  }
  .label--hadith { --bg: var(--hadith); --band: var(--hadith-band); }
  .label--dua { --bg: var(--dua); --band: var(--dua-band); --accent: var(--gold-deep); --title: var(--ink-dark); border: 1px solid var(--rule); color: var(--ink-dark); }
  .label--jar { transform: scale(0.685); transform-origin: 0 0; }

  .label .mark { position: absolute; left: 107px; top: 44px; width: 22px; height: 22px; border-radius: 50%; background: var(--accent); }
  .label .brand { position: absolute; top: 71px; width: 100%; font: 600 10.2px/1 "Quicksand", sans-serif; color: var(--accent); }
  .label .title { position: absolute; top: 86px; width: 100%; font: 300 19px/1 "Raleway", sans-serif; color: var(--title); text-transform: uppercase; }
  .label .sub { position: absolute; top: 106px; width: 100%; font: 300 10px/1 "Raleway", sans-serif; color: var(--title); text-transform: uppercase; }

  .moods { position: absolute; left: 9px; top: 124px; width: 219px; display: flex; list-style: none; }
  .moods li {
    flex: 1; min-width: 0; height: 10px; padding-top: 3.5px; background: var(--band);
    border-top: 3px solid var(--c); font: 500 2.6px/1 "Montserrat", sans-serif;
    text-transform: uppercase; color: #ffffff; white-space: nowrap;
  }
  .label--dua .moods li { color: var(--ink-dark); }
  .moods li:first-child { border-radius: 3px 0 0 3px; }
  .moods li:last-child { border-radius: 0 3px 3px 0; }
  .moods li:nth-child(1) { --c: var(--m-happiness); }
  .moods li:nth-child(2) { --c: var(--m-sadness); }
  .moods li:nth-child(3) { --c: var(--m-anxiety); }
  .moods li:nth-child(4) { --c: var(--m-gratefulness); }
  .moods li:nth-child(5) { --c: var(--m-patience); }
  .moods li:nth-child(6) { --c: var(--m-hope); }
  .moods li:nth-child(7) { --c: var(--m-forgiveness); }
  .moods li:nth-child(8) { --c: var(--m-love); }

  .label .note { position: absolute; top: 139px; left: 20px; width: 197px; font: 500 3px/1.3 "Montserrat", sans-serif; color: inherit; }

  /* Tote print */
  .tote { position: absolute; top: 879px; width: 152px; height: 176px; --accent: var(--gold-light); }
  .tote--quran { background: var(--quran); }
  .tote--hadith { background: #86692a; }
  .tote--dua { background: #f7f7f7; border: 1px solid var(--rule); --accent: var(--gold-deep); }
  .tote .mark { position: absolute; left: 104px; top: 131px; width: 12px; height: 12px; border-radius: 50%; background: var(--accent); }
  .tote .brand { position: absolute; left: 70px; top: 146px; width: 80px; text-align: center; font: 600 6px/1 "Quicksand", sans-serif; color: var(--accent); }
</style>
</head>
<body>
<main class="sheet">

  <!-- Jar labels -->
  <section class="label label--jar label--quran" style="left:197px; top:203px;">
    <span class="mark"></span>
    <p class="brand">Serene Verses</p>
    <h2 class="title">Quran</h2>
    <p class="sub">Jar</p>
    <ul class="moods"><li>Happiness</li><li>Sadness</li><li>Anxiety</li><li>Gratefulness</li><li>Patience</li><li>Hope</li><li>Forgiveness</li><li>Love</li></ul>
    <p class="note">Draw one slip each morning and let its words guide your day, read it slowly, share it with family and return it to the jar to reflect once again.</p>
  </section>
  <section class="label label--jar label--hadith" style="left:473px; top:203px;">
    <span class="mark"></span>
    <p class="brand">Serene Verses</p>
    <h2 class="title">Hadith</h2>
    <p class="sub">Jar</p>
    <ul class="moods"><li>Happiness</li><li>Sadness</li><li>Anxiety</li><li>Gratefulness</li><li>Patience</li><li>Hope</li><li>Forgiveness</li><li>Love</li></ul>
    <p class="note">Draw one slip each morning and let its words guide your day, read it slowly, share it with family and return it to the jar to reflect once again.</p>
  </section>
  <section class="label label--jar label--dua" style="left:751px; top:203px;">
    <span class="mark"></span>
    <p class="brand">Serene Verses</p>
    <h2 class="title">Dua</h2>
    <p class="sub">Jar</p>
    <ul class="moods"><li>Happiness</li><li>Sadness</li><li>Anxiety</li><li>Gratefulness</li><li>Patience</li><li>Hope</li><li>Forgiveness</li><li>Love</li></ul>
    <p class="note">Draw one slip each morning and let its words guide your day, read it slowly, share it with family and return it to the jar to reflect once again.</p>
  </section>

  <div class="divider divider--one"></div>

  <!-- Flat labels -->
  <section class="label label--quran" style="left:191px; top:520px;">
    <span class="mark"></span>
    <p class="brand">Serene Verses</p>
    <h2 class="title">Quran</h2>
    <p class="sub">Jar</p>
    <ul class="moods"><li>Happiness</li><li>Sadness</li><li>Anxiety</li><li>Gratefulness</li><li>Patience</li><li>Hope</li><li>Forgiveness</li><li>Love</li></ul>
    <p class="note">Draw one slip each morning and let its words guide your day, read it slowly, share it with family and return it to the jar to reflect once again.</p>
  </section>
  <section class="label label--hadith" style="left:445px; top:520px;">
    <span class="mark"></span>
    <p class="brand">Serene Verses</p>
    <h2 class="title">Hadith</h2>
    <p class="sub">Jar</p>
    <ul class="moods"><li>Happiness</li><li>Sadness</li><li>Anxiety</li><li>Gratefulness</li><li>Patience</li><li>Hope</li><li>Forgiveness</li><li>Love</li></ul>
    <p class="note">Draw one slip each morning and let its words guide your day, read it slowly, share it with family and return it to the jar to reflect once again.</p>
  </section>
  <section class="label label--dua" style="left:699px; top:520px;">
    <span class="mark"></span>
    <p class="brand">Serene Verses</p>
    <h2 class="title">Dua</h2>
    <p class="sub">Jar</p>
    <ul class="moods"><li>Happiness</li><li>Sadness</li><li>Anxiety</li><li>Gratefulness</li><li>Patience</li><li>Hope</li><li>Forgiveness</li><li>Love</li></ul>
    <p class="note">Draw one slip each morning and let its words guide your day, read it slowly, share it with family and return it to the jar to reflect once again.</p>
  </section>

  <div class="divider divider--two"></div>

  <!-- Tote prints -->
  <section class="tote tote--quran" style="left:216px;">
    <span class="mark"></span>
    <p class="brand">Serene Verses</p>
  </section>
  <section class="tote tote--hadith" style="left:490px;">
    <span class="mark"></span>
    <p class="brand">Serene Verses</p>
  </section>
  <section class="tote tote--dua" style="left:769px;">
    <span class="mark"></span>
    <p class="brand">Serene Verses</p>
  </section>

</main>
</body>
</html>
```